Building company buisness cards

We are looking for a sharp modern new look for our business cards.
We are a New Zealand based company that specialises in house and land packages.
We have attached a photo of the current logo and would like to see if it can be improved somehow if needed.
We are open to any colours but we have chosen green at this stage.
Feel free to change the font and make the logo smarter looking.
Play with the colours and see what looks best.

We want a card that looks so good know one will want to throw it away!

Target Market(s)

Home buyers

Industry/Entity Type

Building

Contact Information for Business Card

Derek Tolvane
0217394062
dtolvane@quillmarkhomesteads.co.nz
quillmarkhomesteads.co.nz

Font styles to use
Serif
Sans Serif

Colors

Designer to choose colors to be used in the design.

Requirements
Must have
• Logo and company name on one side, details on the other side
Nice to have
• Color codes for the original green are HEX #4a8028, RGB(74,128,40), CMYK(42,0,69,50)
• Round corners, Raised and/or spot UV

```html
<!DOCTYPE html>
<html lang="en">
<head>
<meta charset="utf-8">
<title>Quillmark Homesteads — Business Cards</title>
<link href="https://fonts.googleapis.com/css2?family=Montserrat:wght@600;800&family=Roboto:wght@400&display=swap" rel="stylesheet">
<style>
  :root {
    --brand-green: #4a8028;
    --paper-white: #ffffff;
    --arc-grey: #7a7a7a;
    --backdrop: #b4b4b4;
    --radius: 18px;
  }
  * { box-sizing: border-box; margin: 0; padding: 0; }
  html, body { width: 1200px; height: 930px; overflow: hidden; }
  body {
    background: var(--backdrop);
    position: relative;
    font-family: "Roboto", sans-serif;
  }
  .card {
    position: absolute;
    width: 520px;
    height: 300px;
    border-radius: var(--radius);
    overflow: hidden;
  }
  .card--front {
    left: 110px; top: 110px;
    background: var(--brand-green);
    color: var(--paper-white);
  }
  .card--back {
    left: 570px; top: 520px;
    background: var(--paper-white);
  }
  .wordmark {
    font-family: "Montserrat", sans-serif;
    font-weight: 800;
    line-height: 0.95;
    letter-spacing: -0.5px;
    text-align: center;
  }
  .card--front .wordmark {
    position: absolute;
    left: 0; right: 0; top: 88px;
    font-size: 40px;
    color: var(--paper-white);
  }
  .card--front .website {
    position: absolute;
    left: 0; right: 0; bottom: 34px;
    text-align: center;
    font-size: 12px;
    letter-spacing: 0.4px;
  }
  .back-curve { position: absolute; inset: 0; }
  .card--back .wordmark {
    position: absolute;
    right: 40px; top: 62px;
    font-size: 32px;
    color: var(--brand-green);
  }
  .contact {
    position: absolute;
    left: 40px; bottom: 28px;
    color: var(--paper-white);
  }
  .contact__name {
    font-family: "Montserrat", sans-serif;
    font-weight: 600;
    font-size: 22px;
  }
  .contact__role { font-size: 12px; margin-top: 2px; }
  .contact__rule {
    width: 60px; height: 1px;
    background: var(--paper-white);
    margin: 10px 0 9px;
  }
  .contact__list { list-style: none; font-size: 12px; }
  .contact__list li {
    display: flex; align-items: center; gap: 8px;
    margin-top: 4px;
  }
  .contact__list svg { width: 11px; height: 11px; flex: none; }
</style>
</head>
<body>

  <section class="card card--front" aria-label="Card front">
    <div class="wordmark">quillmark<br>homesteads.</div>
    <p class="website">www.quillmarkhomesteads.co.nz</p>
  </section>

  <section class="card card--back" aria-label="Card back">
    <svg class="back-curve" viewBox="0 0 520 300" preserveAspectRatio="none" aria-hidden="true">
      <path d="M112,0 C150,168 330,222 520,182" fill="none" stroke="var(--arc-grey)" stroke-width="7"/>
      <path d="M0,0 L104,0 C142,174 330,232 520,194 L520,300 L0,300 Z" fill="var(--brand-green)"/>
    </svg>
    <div class="wordmark">quillmark<br>homesteads.</div>

    <div class="contact">
      <p class="contact__name">Derek Tolvane</p>
      <p class="contact__role">Founder</p>
      <div class="contact__rule"></div>
      <ul class="contact__list">
        <li>
          <svg viewBox="0 0 12 12" aria-hidden="true"><path d="M2.5 1 L4.5 1 L5 3.5 L3.8 4.4 Q5 7 7.6 8.2 L8.5 7 L11 7.5 L11 9.5 Q11 11 9.5 11 Q1 10 1 2.5 Q1 1 2.5 1 Z" fill="#fff"/></svg>
          0217394062
        </li>
        <li>
          <svg viewBox="0 0 12 12" aria-hidden="true"><rect x="1" y="2.5" width="10" height="7" fill="none" stroke="#fff" stroke-width="1.2"/><path d="M1 2.5 L6 6.5 L11 2.5" fill="none" stroke="#fff" stroke-width="1.2"/></svg>
          dtolvane@quillmarkhomesteads.co.nz
        </li>
        <li>
          <svg viewBox="0 0 12 12" aria-hidden="true"><circle cx="6" cy="6" r="5" fill="none" stroke="#fff" stroke-width="1.1"/><ellipse cx="6" cy="6" rx="2.2" ry="5" fill="none" stroke="#fff" stroke-width="1"/><path d="M1 6 H11" stroke="#fff" stroke-width="1"/></svg>
          www.quillmarkhomesteads.co.nz
        </li>
      </ul>
    </div>
  </section>

</body>
</html>
```